Velmora Cabinets Letter Head and Email Signature

Hi
I would love a design package for a letterhead, email signature, even update my business card if you like if you can come up with a great idea for my new high end cabinet shop. Velmora Cabinets brings timeless craftsmanship to modern interiors, specializing in high end, custom cabinetry designed for architects and interior designers.

Target Market(s)

high end, luxury market

Industry/Entity Type

cabinet making

Requirements
Must have
• my colours of logo as the theme

```html
<!DOCTYPE html>
<html lang="en">
<head>
<meta charset="utf-8">
<title>Velmora Cabinets – Letterhead and Email Signature</title>
<link href="https://fonts.googleapis.com/css2?family=Poppins:wght@400;500;700&family=Arimo:wght@400&family=Tinos:wght@400&display=swap" rel="stylesheet">
<style>
  :root {
    --board: #d3d4d6;
    --panel: #9b9b9b;
    --paper: #ffffff;
    --green: #4a7c45;
    --green-bright: #3f8a3f;
    --ink: #111111;
    --text: #1d1d1d;
    --muted: #444444;
    --sig-fill: #ececec;
  }
  * { margin: 0; padding: 0; box-sizing: border-box; }
  html, body { width: 1200px; height: 829px; overflow: hidden; }
  body { background: var(--board); position: relative; font-family: "Arimo", Arial, sans-serif; }

  /* Letterhead */
  .letterhead {
    position: absolute; left: 114px; top: 117px; width: 441px; height: 624px;
    background: var(--paper); box-shadow: 0 4px 14px rgba(0,0,0,.25); overflow: hidden;
  }
  .brand-name {
    position: absolute; left: 26px; top: 34px;
    font-family: "Poppins", sans-serif; font-weight: 500; font-size: 25px;
    color: var(--green); letter-spacing: .5px; white-space: nowrap;
  }
  .header-divider { position: absolute; left: 283px; top: 23px; width: 1px; height: 59px; background: var(--green); }
  .header-contacts { position: absolute; left: 291px; top: 23px; list-style: none;
    font-family: "Tinos", serif; font-size: 8.6px; color: var(--muted); line-height: 12px; }
  .header-contacts li { display: flex; align-items: flex-start; gap: 5px; }
  .header-contacts svg { width: 8px; height: 8px; margin-top: 2px; flex: none; }
  .letter-body { position: absolute; left: 67px; top: 154px; width: 310px;
    font-size: 8.3px; line-height: 9.95px; color: var(--text); text-align: justify; }
  .letter-body p { margin-bottom: 19.5px; }
  .signature-area { position: absolute; left: 67px; top: 528px; width: 150px; height: 36px;
    background: var(--sig-fill); border-radius: 3px; }
  .footer-waves { position: absolute; left: 0; bottom: 0; width: 441px; height: 60px; }

  /* Email signature */
  .signature-panel { position: absolute; left: 640px; top: 199px; width: 461px; height: 196px; background: var(--panel); }
  .email-signature { position: absolute; left: 18px; top: 25px; width: 412px; height: 138px;
    background: var(--paper); box-shadow: 0 2px 8px rgba(0,0,0,.25); overflow: hidden;
    font-family: "Poppins", sans-serif; }
  .person-name { position: absolute; left: 20px; top: 18px; font-weight: 700; font-size: 16.5px; color: var(--green); }
  .person-title { position: absolute; left: 22px; top: 37px; font-size: 9.3px; color: var(--ink); }
  .sig-contacts { position: absolute; left: 18px; top: 63px; list-style: none; font-size: 10.5px; color: var(--ink); line-height: 15.2px; }
  .sig-contacts li { display: flex; align-items: center; gap: 5px; }
  .sig-contacts svg { width: 11px; height: 11px; flex: none; }
  .sig-brand { position: absolute; left: 262px; top: 42px; width: 130px;
    font-weight: 500; font-size: 22px; line-height: 24px;
    color: var(--green); letter-spacing: .3px; }
  .sig-brand span { display: block; white-space: nowrap; }
  .sig-bar { position: absolute; left: 0; bottom: 0; width: 412px; height: 16px; }
  .bar-address { position: absolute; left: 12px; bottom: 2px; display: flex; align-items: center; gap: 6px;
    font-size: 10px; color: #fff; white-space: nowrap; }
  .bar-address svg { width: 8px; height: 9px; }
  .bar-handle { position: absolute; left: 297px; bottom: 2px; display: flex; align-items: center; gap: 2px;
    font-size: 9px; color: #fff; white-space: nowrap; }
  .handle-dot { width: 6px; height: 6px; border-radius: 50%; background: var(--green-bright); }
</style>
</head>
<body>

<section class="letterhead" aria-label="Letterhead">
  <div class="brand-name">Velmora Cabinets</div>
  <div class="header-divider"></div>
  <ul class="header-contacts">
    <li><svg viewBox="0 0 10 10"><path d="M2 1l2 2-1 1.2c.6 1.2 1.6 2.2 2.8 2.8L7 6l2 2-1.4 1.4C4.6 9 1 5.4.6 2.4z" fill="var(--green)"/></svg>0400 123 456</li>
    <li><svg viewBox="0 0 10 10"><rect x="0.5" y="2" width="9" height="6.5" fill="var(--green)"/><path d="M.5 2l4.5 3.5L9.5 2" stroke="#fff" stroke-width=".8" fill="none"/></svg>info@velmoracabinets.com.au</li>
    <li><svg viewBox="0 0 10 10"><circle cx="5" cy="5" r="4.3" fill="var(--green)"/><path d="M1 5h8M5 .7c-2 2.5-2 6 0 8.6M5 .7c2 2.5 2 6 0 8.6" stroke="#fff" stroke-width=".6" fill="none"/></svg>www.websitename.com</li>
    <li><svg viewBox="0 0 10 10"><path d="M5 .5a3.3 3.3 0 0 1 3.3 3.3C8.3 6.3 5 9.5 5 9.5S1.7 6.3 1.7 3.8A3.3 3.3 0 0 1 5 .5z" fill="var(--green)"/><circle cx="5" cy="3.8" r="1.2" fill="#fff"/></svg><span>421, Address line here<br>Country Name, 45452</span></li>
  </ul>

  <div class="letter-body">
    <p>Lorem ipsum dolor sit amet, consectetur adipiscing elit. Donec fringilla neque euismod volutpat cursus. Vestibulum ac pretium orci, consequat elementum velit. Etiam bibendum purus ac augue finibus volutpat. Vestibulum justo nisl</p>
    <p>Lorem ipsum dolor sit amet, consectetur adipiscing elit. Donec fringilla neque euismod volutpat cursus. Vestibulum ac pretium orci, consequat elementum velit. Etiam bibendum purus ac augue finibus volutpat. Vestibulum justo nisl</p>
    <p>Lorem ipsum dolor sit amet, consectetur adipiscing elit. Donec fringilla neque euismod volutpat cursus. Vestibulum ac pretium orci, consequat elementum velit. Etiam bibendum purus ac augue finibus volutpat. Vestibulum justo nisl, gravida aliquet sollicitudin ut, finibus vitae mi. Praesent aliquet scelerisque blandit. Sed id varius lacus, id tristique sem. Fusce et lobortis leo. Aliquam mollis pellentesque magna, condimentum ullamcorper ex ullamcorper non. Morbi ultricies nunc eu tellus dignissim, eget venenatis dolor ullamcorper. Etiam dolor eros, iaculis at ultricies nec, volutpat nec orci. Vivamus tincidunt rutrum sapien, ac porttitor mauris tristique nec.</p>
    <p>Lorem ipsum dolor sit amet, consectetur adipiscing elit. Donec fringilla neque euismod volutpat cursus. Vestibulum ac pretium orci, consequat elementum velit. Etiam bibendum purus ac augue finibus volutpat. Vestibulum justo nisl, gravida aliquet sollicitudin ut, finibus vitae mi. Praesent aliquet scelerisque blandit. Sed id varius lacus, id tristique sem. Fusce et lobortis leo. Aliquam mollis pellentesque magna, condimentum ullamcorper ex ullamcorper non. Morbi ultricies nunc eu tellus dignissim, eget venenatis dolor ullamcorper. Etiam dolor eros, iaculis at ultricies nec, volutpat nec orci. Vivamus tincidunt rutrum sapien, ac porttitor mauris tristique nec.</p>
    <p>Lorem ipsum dolor sit amet, consectetur adipiscing elit. Donec fringilla neque euismod volutpat cursus. Vestibulum ac pretium orci, consequat elementum velit. Etiam bibendum purus ac augue finibus volutpat. Vestibulum justo nisl</p>
  </div>

  <div class="signature-area" role="img" aria-label="Handwritten signature of the sender"></div>

  <svg class="footer-waves" viewBox="0 0 441 60" preserveAspectRatio="none" aria-hidden="true">
    <path d="M0 22C60 12 150 18 220 30 C300 44 380 48 441 30 L441 60 L0 60Z" fill="var(--ink)"/>
    <path d="M0 12C50 2 120 6 150 14 C100 8 45 10 0 20Z" fill="var(--green)"/>
    <path d="M296 42C360 41 410 36 441 22 L441 28 C410 40 360 44 296 43Z" fill="var(--green)"/>
  </svg>
</section>

<section class="signature-panel" aria-label="Email signature">
  <div class="email-signature">
    <div class="person-name">Rowan Castell</div>
    <div class="person-title">Director Craftsman</div>
    <ul class="sig-contacts">
      <li><svg viewBox="0 0 10 10"><circle cx="5" cy="5" r="5" fill="var(--green-bright)"/><path d="M3.2 2.2l1 1-.6.7c.4.8 1 1.4 1.8 1.8l.7-.6 1 1-.8.8C4.6 6.7 3.3 5.4 2.4 3z" fill="#fff"/></svg>0400 123 456</li>
      <li><svg viewBox="0 0 10 10"><circle cx="5" cy="5" r="5" fill="var(--green-bright)"/><rect x="2.5" y="3.3" width="5" height="3.6" fill="none" stroke="#fff" stroke-width=".7"/><path d="M2.5 3.3L5 5.3l2.5-2" stroke="#fff" stroke-width=".7" fill="none"/></svg>info@velmoracabinets.com.au</li>
      <li><svg viewBox="0 0 10 10"><circle cx="5" cy="5" r="5" fill="var(--green-bright)"/><circle cx="5" cy="5" r="2.7" fill="none" stroke="#fff" stroke-width=".7"/><path d="M2.3 5h5.4M5 2.3v5.4" stroke="#fff" stroke-width=".5"/></svg>www.websitename.com</li>
    </ul>
    <div class="sig-brand"><span>Velmora</span><span>Cabinets</span></div>
    <svg class="sig-bar" viewBox="0 0 412 16" preserveAspectRatio="none" aria-hidden="true">
      <polygon points="0,0 270,0 262,16 0,16" fill="var(--green)"/>
      <polygon points="275,0 412,0 412,16 267,16" fill="var(--ink)"/>
    </svg>
    <div class="bar-address"><svg viewBox="0 0 10 11"><path d="M5 .5a4 4 0 0 1 4 4C9 7.5 5 10.5 5 10.5S1 7.5 1 4.5a4 4 0 0 1 4-4z" fill="#fff"/><circle cx="5" cy="4.5" r="1.4" fill="var(--green)"/></svg>421, Address line here Country Name, 45452</div>
    <div class="bar-handle"><span class="handle-dot"></span>@velmora.cabinets</div>
  </div>
</section>

</body>
</html>
```